KR Appraisals website redesign

I would like to refresh my existing website of www.krappraisals-example.com with new graphics, look and feel, as well as updated structure and wording. Content and layout changes have been uploaded to this project Brief.

My existing website has a dark feel. I am now looking for a light and energetic feel. Financial Services is my industry, so the website should be reflect that. I would also like to reflect the concepts of Trust, Service and Expertise.

The website must be serious and upmarket.

Target Market(s)

Corporate board members, CFO's, treasurers and controllers
Auditors, tax advisors, private equity and venture capital asset managers, investors, tax authorities

Industry/Entity Type

Financial Service

Coding

Coded - Design and coding required

Number of Pages Required

5+ page

Font styles to use
Sans Serif
Other font styles liked:
• Designer can choose another modern font

Colors
0355a3
3277b5
85acd3
eaf1f7
f37122
f68d4d
9bcb3c
acd037
cadf82

Requirements
Must have
• Good hi resolution pictures that convey "Finance", "Trust", "Service" or "Expertise".
• An anti-bot (such as Captcha) mechanism in the contact form.
Should not have
• Must not have all content on one rolling screen.

```html
<!DOCTYPE html>
<html lang="en">
<head>
<meta charset="utf-8">
<title>KR Appraisals – Meet the Team</title>
<link href="https://fonts.googleapis.com/css2?family=Nunito:wght@700;800&family=Varela+Round&display=swap" rel="stylesheet">
<style>
  :root {
    --blue: #0355a3;
    --orange: #f37122;
    --green: #9bcb3c;
    --text: #555555;
    --muted: #777777;
    --rule: #e2e2e2;
    --footer-bg: #333333;
    --footer-text: #9a9a9a;
    --white: #ffffff;
  }
  * { margin: 0; padding: 0; box-sizing: border-box; }
  html, body { width: 757px; height: 1200px; overflow: hidden; background: var(--white); }
  body { position: relative; font-family: "Varela Round", sans-serif; color: var(--text); }

  .site-header {
    position: absolute; left: 0; top: 0; width: 757px; height: 63px;
    background: linear-gradient(90deg, #e6e7df 0%, #eeeee4 50%, #f7f8e9 100%);
  }
  .brand {
    position: absolute; left: 102px; top: 22px;
    font-family: "Varela Round", sans-serif; font-size: 15px; color: #6f6f6f;
    letter-spacing: .3px; text-transform: uppercase;
  }
  .main-nav { position: absolute; top: 28px; left: 385px; display: flex; gap: 0; }
  .main-nav a {
    font-family: "Nunito", sans-serif; font-weight: 700; font-size: 7px;
    color: #6a6a6a; text-decoration: none; text-transform: uppercase; margin-right: 25px;
  }
  .main-nav a.is-active { color: var(--blue); }

  .page-title {
    position: absolute; top: 115px; left: 0; width: 757px; text-align: center;
    font-family: "Nunito", sans-serif; font-weight: 800; font-size: 25px;
    color: var(--orange); letter-spacing: .2px;
  }

  .member { position: absolute; left: 102px; width: 555px; }
  .member-photo { position: absolute; left: 0; top: 0; width: 123px; height: 123px; }
  .member-body { position: absolute; left: 144px; top: 0; width: 412px; }
  .member-name {
    font-family: "Nunito", sans-serif; font-weight: 800; font-size: 14px;
    color: var(--blue); line-height: 18px;
  }
  .member-role { font-size: 7px; color: var(--muted); line-height: 12.5px; margin-top: 1px; }
  .member-field { font-size: 7px; color: var(--green); line-height: 12.5px; }
  .member-bio { font-size: 7px; line-height: 12.35px; color: var(--text); margin-top: 12px; }
  .member-bio.tight { margin-top: 2px; }
  .divider { position: absolute; left: 102px; width: 555px; height: 1px; background: var(--rule); }

  .site-footer { position: absolute; left: 0; top: 978px; width: 757px; height: 222px; }
  .footer-shape { position: absolute; left: 0; top: 0; }
  .footer-brand {
    position: absolute; top: 48px; width: 757px; text-align: center;
    font-size: 15px; color: #8a8a8a; text-transform: uppercase; letter-spacing: .3px;
  }
  .footer-nav {
    position: absolute; left: 102px; top: 94px; width: 555px; height: 29px;
    border-top: 1px solid #555; border-bottom: 1px solid #555;
    display: flex; justify-content: center; align-items: center; padding-left: 0;
  }
  .footer-nav a {
    font-family: "Nunito", sans-serif; font-weight: 700; font-size: 7px;
    color: #8d8d8d; text-decoration: none; text-transform: uppercase; margin: 0 12.5px;
  }
  .footer-nav a.is-active { color: var(--green); }
  .footer-col { position: absolute; top: 138px; font-size: 6.5px; color: var(--footer-text); }
  .footer-col h4 {
    font-family: "Nunito", sans-serif; font-weight: 800; font-size: 8.5px;
    color: var(--orange); margin-bottom: 9px; text-transform: uppercase;
  }
  .footer-col p { line-height: 14px; }
  .footer-col .hl { color: var(--green); }
  .footer-col .wh { color: #e6e6e6; }
  .contact-line { display: flex; align-items: flex-start; gap: 5px; line-height: 10.5px; margin-bottom: 8px; }
  .badge { position: absolute; top: 154px; height: 18px; border-radius: 3px; background: #5a5a5a; }
</style>
</head>
<body>

<header class="site-header">
  <div class="brand">KR Appraisals</div>
  <nav class="main-nav">
    <a href="#">Home</a>
    <a href="#" class="is-active">About</a>
    <a href="#">Services</a>
    <a href="#">News &amp; Views</a>
    <a href="#">Contact</a>
  </nav>
</header>

<h1 class="page-title">MEET THE TEAM</h1>

<section class="member" style="top:173px">
  <div class="member-photo" role="img" aria-label="Portrait photo of Martin Hale" style="background:linear-gradient(160deg,#e9e3de 0%,#c9a894 45%,#2c3346 100%)"></div>
  <div class="member-body" style="top:-2px">
    <h2 class="member-name">Martin Hale</h2>
    <p class="member-role">Managing Director</p>
    <p class="member-field">Business &amp; Intellectual Property Valuations</p>
    <p class="member-bio">"Martin Hale is a business and intangible asset valuation advisor with more than 20 years of investment industry experience and more than 15 years of valuation advisory and corporate finance experience. His primary areas of focus include purchase price allocations (PPA), impairment testing, shareholder disputes, tax and transaction-related valuations, fair value, portfolio risk measurement services and M&amp;A advisory. Martin has been involved in cross-border valuation issues in America, Europe, Middle East, Central Asia and Africa. He is a CVA charterholder, NRVA Register Valuator and SVP accredited senior appraiser in business valuation where he is also a founding executive board member of SVP's Europe Chapter and Vice President of SVP Europe responsible for the Benelux region. He is a member of the Business Valuation Resource Panel at the Valuation Standards Council in Washington DC. Martin is a lecturer at Harbourtown University where he developed the CVA Prep program and appears as a guest lecturer at several Dutch universities on valuation topics.</p>
  </div>
</section>
<div class="divider" style="top:377px"></div>

<section class="member" style="top:410px">
  <div class="member-photo" role="img" aria-label="Black and white portrait photo of Joost van Rijn" style="background:linear-gradient(160deg,#f0f0f0 0%,#b8b8b8 50%,#222 100%)"></div>
  <div class="member-body" style="top:-2px">
    <h2 class="member-name">Joost van Rijn</h2>
    <p class="member-field">Transfer Pricing</p>
    <p class="member-bio" style="margin-top:15px">Joost van Rijn (Netherlands) has broad experience in international tax consulting since 1992, particularly in the transfer pricing area. He has been involved in numerous transfer pricing projects, e.g. IP (re)structuring, documentation, valuations, financial services and dispute resolution. Joost has written a number of articles for publications such as Global Transfer Pricing Review, Tax Practice Pricing Bulletin and Finance Leader Quarterly. He has been named numerous times as one of the Region's Leading Transfer Pricing Advisors. Joost has taught transfer pricing and risk management courses for organizations such as Westmere University and the ITFA.</p>
  </div>
</section>
<div class="divider" style="top:566px"></div>

<section class="member" style="top:600px">
  <div class="member-photo" role="img" aria-label="Portrait photo of Glen Porter" style="background:linear-gradient(160deg,#4b544f 0%,#c99a7e 45%,#1f2228 100%)"></div>
  <div class="member-body" style="top:-2px">
    <h2 class="member-name">Glen Porter</h2>
    <p class="member-field">Machinery &amp; Equipment Valuations</p>
    <p class="member-bio" style="margin-top:10px">Glen Porter (New York) is CEO of PV Valuation Group and has 34 years experience with International valuation firms. He lived and worked in China, was CEO of a valuation business in Japan, and helped start an operation in Singapore. Glen is an SVP and MRIVS designated valuer. He has an academic degree in Valuation Sciences from Eastbrook University, and is a frequent speaker and author on valuation topics worldwide. Glen serves on the Board of the Global Institute of Valuation Professionals (GIVP), and Chairs the GIVP Marketing Committee, is past editor of the SVP Machinery &amp; Technical Specialties Journal, and past member of RIVS Americas Plant Machinery Committee.</p>
  </div>
</section>
<div class="divider" style="top:762px"></div>

<section class="member" style="top:795px">
  <div class="member-photo" role="img" aria-label="Portrait photo of Sander Vermeer" style="background:linear-gradient(160deg,#f2f2f2 0%,#c79d84 45%,#1d2640 100%)"></div>
  <div class="member-body" style="top:-2px">
    <h2 class="member-name">Sander Vermeer</h2>
    <p class="member-field">Machinery &amp; Equipment Valuations</p>
    <p class="member-bio tight">Sander Vermeer is a specialist in fixed asset valuations which covers a broad range of applications including: insurance placement values, financial reporting, tax purposes, fixed asset leases, restructuring, acquisitions, and divestitures. He has performed valuation services since 2004 for companies with facilities across Europe, the Americas, Middle East, Africa, Asia, and Australia. He is a Registered Valuer of the Royal Institute of Valuation Surveyors (RIVS) where he co-chairs the Machinery and Business Assets committee in the Netherlands.</p>
  </div>
</section>

<footer class="site-footer">
  <svg class="footer-shape" width="757" height="222" viewBox="0 0 757 222" aria-hidden="true">
    <polygon points="0,44 378.5,0 757,44 757,222 0,222" fill="#333333"/>
  </svg>
  <div class="footer-brand">KR Appraisals</div>
  <nav class="footer-nav">
    <a href="#" class="is-active">Home</a>
    <a href="#">About</a>
    <a href="#">Services</a>
    <a href="#">News &amp; Views</a>
    <a href="#">Contact</a>
  </nav>
  <div class="footer-col" style="left:103px">
    <h4>Credits</h4>
    <p>© 2019 <span class="hl">KR Appraisals B.V.</span></p>
    <p>Logo by <span class="wh">Lotte Brandsma</span></p>
    <p>Website by <span class="hl">Northline Web Studio</span></p>
  </div>
  <div class="footer-col" style="left:294px">
    <h4>Leiden</h4>
    <div class="contact-line">
      <svg width="6" height="8" viewBox="0 0 12 16"><path d="M6 0C2.7 0 0 2.6 0 5.9 0 10.3 6 16 6 16s6-5.7 6-10.1C12 2.6 9.3 0 6 0zm0 8.2A2.3 2.3 0 1 1 6 3.6a2.3 2.3 0 0 1 0 4.6z" fill="#9bcb3c"/></svg>
      <span>Havenstraat 48<br>2311 AB Leiden</span>
    </div>
    <div class="contact-line">
      <svg width="8" height="8" viewBox="0 0 16 16"><path d="M3.6 1.2 6 3.8c.4.4.4 1 0 1.4L4.8 6.6a10 10 0 0 0 4.6 4.6L10.8 10c.4-.4 1-.4 1.4 0l2.6 2.4c.4.4.4 1 0 1.4l-1.4 1.4C11 17 0 6 1.8 3.2L3.2 1.2c.1-.2.3-.2.4 0z" fill="#9bcb3c"/></svg>
      <span class="wh" style="font-size:7px">070 555 0142</span>
    </div>
  </div>
  <div class="badge" role="img" aria-label="Partner badge" style="left:485px;width:78px"></div>
  <div class="badge" role="img" aria-label="Membership badge" style="left:577px;width:78px;height:26px;top:150px"></div>
</footer>

</body>
</html>
```